Meridale Bed Company Needs Business Card

Looking for a very nice looking business card. Creative but not extravagant. We sell beds and pillows across the U.S. and need something professional but catchy. I have attached the logo.

Name : Devin Holt
Title : President
Phone : (800) 471-2960
Email: sleep@quilmora.com
Website: www.quilmora.com

Can be single-sided or double-sided
horizontal or vertical

Can use Blues/Greys

Target Market(s)

Mass Market

Industry/Entity Type

Retail

Contact Information for Business Card

Name : Devin Holt
Title : President
Phone : (800) 471-2960
Email: sleep@quilmora.com
Website: www.quilmora.com

Requirements
Must have
• Clean, Modern, Smooth
• Can use Blues/Greys
• On the other side without the information - have something simple like www.quilmora.com or our logo
Nice to have
• Surprise me
Should not have
• Nothing crazy, nothing cluttered

```html
<!DOCTYPE html>
<html lang="en">
<head>
<meta charset="utf-8">
<title>Meridale Bed Company — Business Card</title>
<link rel="stylesheet" href="https://fonts.googleapis.com/css2?family=Arimo:wght@400;700&display=swap">
<style>
  :root {
    --backdrop: #2b2522;
    --card: #4f4f50;
    --card-edge: #444445;
    --wordmark-grey: #c9c9c9;
    --accent-blue: #2e9be0;
    --text-white: #f2f2f2;
    --divider: #d8d8d8;
  }
  html, body {
    margin: 0;
    padding: 0;
    width: 1200px;
    height: 769px;
    overflow: hidden;
    background: var(--backdrop);
  }
  .sheet {
    position: relative;
    width: 1200px;
    height: 769px;
    display: flex;
    align-items: center;
    justify-content: center;
    gap: 40px;
  }
  .card {
    position: relative;
    width: 540px;
    height: 309px;
    background: var(--card);
    border: 1px solid var(--card-edge);
    box-sizing: border-box;
    overflow: hidden;
  }
  .wordmark {
    font-family: "Arimo", sans-serif;
    font-weight: 400;
    line-height: 1;
    white-space: nowrap;
  }
  .card-back .wordmark {
    position: absolute;
    left: 0;
    right: 0;
    top: 112px;
    text-align: center;
    font-size: 72px;
    color: var(--wordmark-grey);
  }
  .card-front .wordmark {
    position: absolute;
    right: 48px;
    top: 72px;
    font-size: 64px;
    color: var(--accent-blue);
  }
  .identity {
    position: absolute;
    left: 106px;
    top: 196px;
    width: 140px;
    text-align right;
    text-align: right;
    font-family: "Arimo", sans-serif;
  }
  .identity .name {
    font-weight: 700;
    font-size: 19px;
    color: var(--accent-blue);
    margin: 0;
  }
  .identity .title {
    font-size: 17px;
    color: var(--text-white);
    margin: 4px 0 0;
  }
  .divider {
    position: absolute;
    left: 262px;
    top: 188px;
    width: 1px;
    height: 72px;
    background: var(--divider);
  }
  .contacts {
    position: absolute;
    left: 280px;
    top: 190px;
    margin: 0;
    padding: 0;
    list-style: none;
    font-family: "Arimo", sans-serif;
    font-size: 15px;
    color: var(--text-white);
  }
  .contacts li {
    display: flex;
    align-items: center;
    gap: 9px;
    height: 23px;
  }
  .contacts svg {
    width: 14px;
    height: 14px;
    flex: none;
  }
</style>
</head>
<body>
<main class="sheet">
  <section class="card card-back" aria-label="Card back">
    <div class="wordmark">quilmora</div>
  </section>

  <section class="card card-front" aria-label="Card front">
    <div class="wordmark">quilmora</div>

    <div class="identity">
      <p class="name">Devin Holt</p>
      <p class="title">President</p>
    </div>

    <div class="divider"></div>

    <ul class="contacts">
      <li>
        <svg viewBox="0 0 14 14" aria-hidden="true">
          <path fill="var(--accent-blue)" d="M3.2 1.2 5.1 3.4 4 5c.8 1.8 2.2 3.2 4 4l1.6-1.1 2.2 1.9-1.1 2.5C6 12 2 8 1.7 2.3z"/>
        </svg>
        <span>(800) 471-2960</span>
      </li>
      <li>
        <svg viewBox="0 0 14 14" aria-hidden="true">
          <rect x="1" y="3" width="12" height="8.5" rx="1" fill="var(--accent-blue)"/>
          <path d="M1.5 3.6 7 8l5.5-4.4" fill="none" stroke="var(--card)" stroke-width="1.2"/>
        </svg>
        <span>sleep@quilmora.com</span>
      </li>
      <li>
        <svg viewBox="0 0 14 14" aria-hidden="true">
          <circle cx="7" cy="7" r="6" fill="var(--accent-blue)"/>
          <path d="M7 1.5v11M1.5 7h11M7 1.5c-2.6 3-2.6 8 0 11M7 1.5c2.6 3 2.6 8 0 11" fill="none" stroke="var(--card)" stroke-width="0.9"/>
        </svg>
        <span>www.quilmora.com</span>
      </li>
    </ul>
  </section>
</main>
</body>
</html>
```